Corporate Business Card

Very professional, Modern, Not to busy, include phone address email, website
(253) 617-4930, 18761 52nd Avenue S, Kent, WA 98047, martin@plumlinegroup.com, varkoworks.com

Target Market(s)

Manufacturing

Industry/Entity Type

Aero, machining, manufacturing, Off road racing

Contact Information for Business Card

Phone, address email, website

```html
<!DOCTYPE html>
<html lang="en">
<head>
<meta charset="utf-8">
<title>Varko Works — Business Card</title>
<link rel="stylesheet" href="https://fonts.googleapis.com/css2?family=Questrial&display=swap">
<style>
  :root {
    --navy: #173572;
    --red: #d4232b;
    --paper: #ffffff;
    --backdrop: #e8e5e1;
  }
  * { margin: 0; padding: 0; box-sizing: border-box; }
  html, body { width: 1200px; height: 1200px; overflow: hidden; }
  body {
    background: var(--backdrop);
    position: relative;
    font-family: "Questrial", sans-serif;
    color: var(--navy);
  }
  .card {
    position: absolute;
    width: 799px;
    height: 456px;
    background: var(--paper);
    box-shadow: 0 6px 18px rgba(0,0,0,0.12);
    overflow: hidden;
  }
  .card--front { left: 337px; top: 99px; }
  .card--back { left: 51px; top: 644px; }
  .card-art { position: absolute; inset: 0; width: 100%; height: 100%; }

  .brand {
    position: absolute;
    left: 0; right: 0;
    display: flex;
    align-items: center;
    justify-content: center;
    gap: 14px;
    color: var(--navy);
    white-space: nowrap;
  }
  .brand-dot { border-radius: 50%; background: var(--red); flex: none; }
  .card--front .brand { top: 190px; font-size: 66px; }
  .card--front .brand-dot { width: 30px; height: 30px; }
  .card--back .brand { top: 98px; font-size: 46px; }
  .card--back .brand-dot { width: 22px; height: 22px; }

  .contact-list {
    position: absolute;
    left: 220px;
    width: 358px;
    top: 312px;
    list-style: none;
    text-align: center;
    font-size: 18.5px;
    line-height: 28.5px;
    letter-spacing: 0.2px;
  }
</style>
</head>
<body>

  <section class="card card--front">
    <div class="brand"><span class="brand-dot"></span>Varko Works</div>
  </section>

  <section class="card card--back">
    <svg class="card-art" viewBox="0 0 799 456" aria-hidden="true">
      <polygon class="side-band" points="0,0 41,0 41,210 0,272" fill="var(--navy)"/>
      <polygon class="side-band" points="758,0 799,0 799,272 758,210" fill="var(--navy)"/>

      <path class="contact-frame" d="M220,456 V297 Q220,266 251,266 H296" fill="none" stroke="var(--navy)" stroke-width="1.6"/>
      <path class="contact-frame" d="M504,266 H547 Q578,266 578,297 V456" fill="none" stroke="var(--navy)" stroke-width="1.6"/>

      <line x1="334" y1="265" x2="464" y2="265" stroke="var(--red)" stroke-width="2"/>

      <g class="icon-phone" transform="translate(317 265)">
        <circle r="17" fill="var(--red)"/>
        <path d="M-6,-7 l3,-1 l2.5,4.5 l-2,2 q1.5,3.5 5,5 l2,-2 l4.5,2.5 l-1,3 q-8,1 -13.5,-6 q-3,-4 -0.5,-8z" fill="none" stroke="#fff" stroke-width="1.5" stroke-linejoin="round"/>
      </g>
      <g class="icon-mail" transform="translate(371 265)">
        <circle r="17" fill="var(--red)"/>
        <rect x="-8.5" y="-6" width="17" height="12" fill="none" stroke="#fff" stroke-width="1.5"/>
        <path d="M-8.5,-6 L0,1 L8.5,-6 M-8.5,6 L-2.5,0 M8.5,6 L2.5,0" fill="none" stroke="#fff" stroke-width="1.3"/>
      </g>
      <g class="icon-pin" transform="translate(426 265)">
        <circle r="17" fill="var(--red)"/>
        <path d="M0,8 C-3,3 -6,0 -6,-3 A6,6 0 0 1 6,-3 C6,0 3,3 0,8z" fill="none" stroke="#fff" stroke-width="1.5"/>
        <circle cy="-3" r="2" fill="#fff"/>
        <path d="M-7,8 H7" stroke="#fff" stroke-width="1.3"/>
      </g>
      <g class="icon-globe" transform="translate(481 265)">
        <circle r="17" fill="var(--red)"/>
        <g fill="none" stroke="#fff" stroke-width="1.2">
          <circle r="8.5"/>
          <ellipse rx="3.8" ry="8.5"/>
          <path d="M-8.5,0 H8.5 M-7.5,-4 H7.5 M-7.5,4 H7.5 M0,-8.5 V8.5"/>
        </g>
      </g>
    </svg>

    <div class="brand"><span class="brand-dot"></span>Varko Works</div>

    <ul class="contact-list">
      <li class="contact-phone">(253) 617-4930, 18761</li>
      <li class="contact-web">varkoworks.com</li>
      <li class="contact-address">52nd Avenue S, Kent, WA 98047</li>
      <li class="contact-email">martin@plumlinegroup.com</li>
    </ul>
  </section>

</body>
</html>
```